QRV Advisors needs a web site

We need a web site for www.qrvadvisors-example.com. QRV is a mergers and acquisition consulting company that focuses our buyer and seller services on logistics companies. We help put companies together, and help with legal and financial due diligence. We want the web site to express our service and show the logistics components. We want personalized images versus pictures of trucks and airplanes.

Our new logo uses Burgandy and grey colors. Image attached. We are not in to bold, big letters...classy, artistic, low key preferred. Confidentiality, experience, professional are what we want to express on the site.

All we expect for the first part of this project is a home page, and one subpage.  We are budgeting other funds for the technical aspects of the web site

Reason: All that I'm seeing so far is trucks, forklifts and planes. We are a legal mergers and acquisitions firm that focus on logistics. I like some of the images to say logistics, but really want it say legal, financial, and putting companies together. Will pay extra for the sub page if someone can impress us with a home page.

Reason: Swamped with another project at the moment...will work on this over the weekend and provide designer feedback and select final design by Tuesday

```html
<!DOCTYPE html>
<html lang="en">
<head>
<meta charset="utf-8">
<title>QRV Advisors – Contact Us</title>
<link rel="stylesheet" href="https://fonts.googleapis.com/css2?family=Open+Sans:wght@400;600&display=swap">
<style>
:root{
  --burgundy:#b00a3c;
  --burgundy-dark:#8e0630;
  --burgundy-light:#c5164c;
  --grey-text:#555555;
  --grey-mid:#8a8a8a;
  --page-top:#e4e4e4;
  --page-bottom:#f3f3f3;
  --field-border:#c9c9c9;
  --charcoal:#272727;
  --band-top:#5a5a5a;
  --band-bottom:#3b3b3b;
  --white:#ffffff;
  --map-tone:#e9e2cf;
}
*{box-sizing:border-box;margin:0;padding:0}
html,body{width:1012px;height:1200px;overflow:hidden}
body{font-family:"Open Sans",Verdana,sans-serif;color:var(--grey-text);background:var(--page-bottom)}
.page{position:absolute;left:0;top:0;width:1020px;height:1210px;transform:scale(.99216);transform-origin:0 0;
  background:linear-gradient(var(--page-top),var(--page-bottom) 760px);border-top:3px solid var(--burgundy);overflow:hidden}
.abs{position:absolute}

/* header */
.nav-bar{left:275px;top:60px;width:699px;height:104px}
.brand-plate{left:57px;top:52px;width:266px;height:140px}
.brand-name{left:68px;top:94px;font-size:27px;font-weight:400;color:#5b5b5b;letter-spacing:1px}
.nav-item{top:60px;height:104px;color:var(--white);font-size:13px;letter-spacing:1px;text-transform:uppercase;
  display:flex;flex-direction:column;align-items:center;justify-content:flex-end;padding-bottom:20px;gap:12px}
.nav-item svg{display:block}
.nav-item.is-active{background:var(--burgundy-dark)}
.caret{font-size:8px;vertical-align:4px;margin-left:3px}

/* contact */
.page-title{left:81px;top:229px;font-size:20px;font-weight:400;letter-spacing:1.5px;color:#4a4a4a}
.intro{left:83px;top:274px;width:400px;font-size:12px;line-height:22px;letter-spacing:.3px}
.field{background:var(--white);border:1px solid var(--field-border);box-shadow:inset 0 1px 3px rgba(0,0,0,.12);
  font-size:12px;color:var(--grey-mid);padding:9px 11px;letter-spacing:.3px}
.btn{display:flex;align-items:center;justify-content:center;color:var(--white);font-size:12.5px;letter-spacing:.5px;border-radius:2px}
.btn-primary{background:linear-gradient(var(--burgundy-light),var(--burgundy-dark));border:1px solid #7a0428}
.btn-dark{background:linear-gradient(#4a4a4a,#222);border:1px solid #111}

.map-frame{left:532px;top:279px;width:427px;height:342px;border:3px solid #c6c6c6;background:var(--map-tone)}
.map-area{position:absolute;inset:0;background:linear-gradient(135deg,#ece6d3,#ddd6c2 60%,#e8e0c8)}
.info-card{left:553px;top:317px;width:196px;height:278px;background:var(--white);box-shadow:0 1px 6px rgba(0,0,0,.3);padding:15px 20px;font-size:10.5px;line-height:16.5px;color:#444}
.info-card h3{font-size:16px;font-weight:400;color:#666;padding-bottom:8px;border-bottom:1px solid #e2e2e2;margin-bottom:8px}
.info-card .link{color:var(--burgundy)}
.info-card .label{font-weight:600;color:#777;font-size:11.5px;margin-top:3px}
.info-card .mini-field{height:22px;background:#f1f1f1;border:1px solid #e0e0e0;margin-top:6px;font-size:10px;font-style:italic;color:#999;padding:2px 6px}
.info-card .mini-btn{margin-top:12px;width:106px;height:23px;font-size:10.5px}
.close-dot{left:729px;top:325px;width:12px;height:12px;border-radius:50%;background:var(--burgundy);color:#fff;font-size:8px;line-height:12px;text-align:center}

/* newsletter */
.newsletter{left:0;top:865px;width:1020px;height:74px;background:linear-gradient(var(--band-top),var(--band-bottom))}
.newsletter-label{left:142px;top:893px;color:var(--white);font-size:15px;letter-spacing:1px}

/* footer */
.footer{left:0;top:939px;width:1020px;height:231px;background:var(--charcoal)}
.footer-heading{top:980px;color:var(--white);font-size:13px;letter-spacing:1px;text-transform:uppercase}
.footer-links{top:1020px;list-style:none;color:#e6e6e6;font-size:11px;letter-spacing:.4px}
.footer-links li{height:25px}
.footer-links li.two-line{height:39px;line-height:13px}
.footer .field,.foot-field{font-size:11px;padding:5px 9px;border:none;box-shadow:none;border-radius:2px;color:#8a8a8a}

.legal-bar{left:0;top:1170px;width:1020px;height:40px;background:var(--burgundy)}
.legal-text{left:82px;top:1184px;color:var(--white);font-size:11px;letter-spacing:.4px}
.social-dot{top:1180px;width:20px;height:20px;border-radius:50%;background:var(--white)}
</style>
</head>
<body>
<div class="page">

  <!-- header -->
  <header>
    <svg class="abs nav-bar" width="699" height="104" viewBox="0 0 699 104" aria-hidden="true">
      <defs><linearGradient id="navGrad" x1="0" y1="0" x2="0" y2="1"><stop offset="0" stop-color="#c4124a"/><stop offset="1" stop-color="#a3083a"/></linearGradient></defs>
      <polygon points="48,0 699,0 699,104 0,104" fill="url(#navGrad)"/>
    </svg>
    <svg class="abs brand-plate" width="266" height="140" viewBox="0 0 266 140" aria-hidden="true">
      <defs>
        <linearGradient id="plateGrad" x1="0" y1="0" x2="0" y2="1"><stop offset="0" stop-color="#f7f7f7"/><stop offset="1" stop-color="#d2d2d2"/></linearGradient>
        <radialGradient id="plateShadow" cx=".4" cy="0" r=".6"><stop offset="0" stop-color="#000" stop-opacity=".22"/><stop offset="1" stop-color="#000" stop-opacity="0"/></radialGradient>
      </defs>
      <ellipse cx="100" cy="118" rx="110" ry="14" fill="url(#plateShadow)"/>
      <polygon points="0,0 266,0 216,115 0,115" fill="url(#plateGrad)" stroke="#c9c9c9"/>
    </svg>
    <div class="abs brand-name">QRV Advisors</div>

    <nav>
      <a class="abs nav-item" style="left:338px;width:60px">
        <svg width="34" height="28" viewBox="0 0 34 28"><path d="M17 2 2 15h4v12h8v-8h6v8h8V15h4z" fill="#fff"/></svg>Home</a>
      <a class="abs nav-item" style="left:430px;width:88px">
        <svg width="42" height="26" viewBox="0 0 42 26"><circle cx="12" cy="8" r="5" fill="#fff"/><circle cx="21" cy="6" r="6" fill="#fff"/><circle cx="30" cy="8" r="5" fill="#fff"/><path d="M3 26c0-8 4-12 9-12s9 4 9 12zM21 26c0-8 4-12 9-12s9 4 9 12zM11 26c0-9 4-13 10-13s10 4 10 13z" fill="#fff"/></svg>About Us</a>
      <a class="abs nav-item" style="left:552px;width:120px">
        <svg width="30" height="30" viewBox="0 0 30 30"><path d="M3 10h7a4 4 0 1 1 7 0h7v7a4 4 0 1 1 0 7v5H3v-7a4 4 0 1 0 0-6z" fill="#fff"/></svg><span>Our Services<span class="caret">▼</span></span></a>
      <a class="abs nav-item" style="left:703px;width:112px">
        <svg width="32" height="32" viewBox="0 0 32 32" fill="#fff"><path d="M16 2 30 9 16 16 2 9z"/><path d="M4 14l12 6 12-6 2 1-14 7-14-7z"/><path d="M4 20l12 6 12-6 2 1-14 7-14-7z"/></svg>Case Studies</a>
      <a class="abs nav-item is-active" style="left:851px;width:104px">
        <svg width="28" height="20" viewBox="0 0 28 20"><rect width="28" height="20" fill="#fff"/><path d="M0 0l14 11L28 0" fill="none" stroke="#8e0630" stroke-width="2"/></svg>Contact Us</a>
    </nav>
  </header>

  <!-- contact -->
  <main>
    <h1 class="abs page-title">CONTACT US</h1>
    <p class="abs intro">Lorem ipsum dolor sit amet, consectetur adipiscing elit. Nam a risus sed justo ullamcorper commodo. Vivamus iaculis purus id ipsum laoreet, sed fermentum mauris posuere.</p>

    <form>
      <div class="abs field" style="left:84px;top:363px;width:197px;height:34px">Firstname</div>
      <div class="abs field" style="left:289px;top:363px;width:197px;height:34px">Email Address</div>
      <div class="abs field" style="left:84px;top:409px;width:197px;height:34px">Contact Number</div>
      <div class="abs field" style="left:289px;top:409px;width:197px;height:34px">Subject</div>
      <div class="abs field" style="left:84px;top:455px;width:401px;height:164px">Message</div>
      <div class="abs btn btn-primary" style="left:84px;top:634px;width:134px;height:36px">Send Message</div>
      <div class="abs btn btn-dark" style="left:228px;top:634px;width:134px;height:36px">Reset Form</div>
    </form>

    <div class="abs map-frame">
      <div class="map-area" role="img" aria-label="Street map showing the office location with map pins"></div>
    </div>
    <svg class="abs" style="left:746px;top:437px" width="30" height="40" viewBox="0 0 30 40" aria-hidden="true"><polygon points="0,0 28,20 0,40" fill="#fff"/></svg>
    <div class="abs info-card">
      <h3>QRV Office</h3>
      <div>1 Lorem Ipsum</div>
      <div>480 Harbor Lane</div>
      <div>Brookfield, ST 00410</div>
      <div>555-010-2040</div>
      <div class="link">http://qrvadvisors-example.com</div>
      <div class="label">Directions</div>
      <div class="mini-field">From:</div>
      <div class="mini-field">To:</div>
      <div class="btn btn-primary mini-btn">Get Directions</div>
    </div>
    <div class="abs close-dot">×</div>
  </main>

  <!-- newsletter -->
  <section class="abs newsletter"></section>
  <div class="abs newsletter-label">SUBSCRIBE TO OUR NEWSLETTER:</div>
  <div class="abs field" style="left:425px;top:889px;width:350px;height:31px;border:none;padding:7px 11px">Email Address</div>
  <div class="abs btn btn-primary" style="left:786px;top:889px;width:90px;height:31px;font-size:11px">SUBSCRIBE</div>

  <!-- footer -->
  <footer>
    <div class="abs footer"></div>
    <h4 class="abs footer-heading" style="left:80px">About Us</h4>
    <h4 class="abs footer-heading" style="left:231px">Services Offered</h4>
    <h4 class="abs footer-heading" style="left:442px">Additional Info</h4>
    <h4 class="abs footer-heading" style="left:642px">Quick Message</h4>

    <ul class="abs footer-links" style="left:83px">
      <li>Who we are</li><li>Client List</li><li>Case Studies</li><li>Contact Info</li>
    </ul>
    <ul class="abs footer-links" style="left:235px">
      <li class="two-line">Strategic Planning<br>&amp; Negotiation</li><li>Legal Documentation</li><li>Due Diligence</li><li>Brokering</li>
    </ul>
    <ul class="abs footer-links" style="left:445px">
      <li>Sitemap</li><li>FAQ</li><li>Privacy Policy</li><li>Terms &amp; Agreement</li>
    </ul>

    <div class="abs field foot-field" style="left:642px;top:1022px;width:137px;height:26px">Firstname</div>
    <div class="abs field foot-field" style="left:642px;top:1056px;width:137px;height:26px">Email Address</div>
    <div class="abs field foot-field" style="left:642px;top:1093px;width:137px;height:26px">Contact #</div>
    <div class="abs field foot-field" style="left:788px;top:1022px;width:138px;height:61px">Message</div>
    <div class="abs btn btn-primary" style="left:789px;top:1093px;width:137px;height:26px;font-size:11.5px">Send Message</div>

    <div class="abs legal-bar"></div>
    <div class="abs legal-text">QRV Advisors All Rights Reserved ® 2014</div>
    <span class="abs social-dot" style="left:842px" aria-label="Social profile"></span>
    <span class="abs social-dot" style="left:871px" aria-label="Social profile"></span>
    <span class="abs social-dot" style="left:901px" aria-label="Social profile"></span>
  </footer>
</div>
</body>
</html>
```